Business Card Design

I already have a company logo for my company. I have a logo for the manufacturer we represent. I want a professional business card design.

```html
<!DOCTYPE html>
<html lang="en">
<head>
<meta charset="utf-8">
<title>Beacon Guard LLC – Business Card</title>
<link rel="stylesheet" href="https://fonts.googleapis.com/css2?family=Open+Sans:wght@400;600;700;800&display=swap">
<style>
  :root {
    --stage: #3a3a3a;
    --stage-dark: #1e1e1e;
    --card: #161616;
    --red: #e31e24;
    --gold: #d9a520;
    --white: #f1f1f1;
    --muted: #d6d6d6;
  }
  * { box-sizing: border-box; margin: 0; padding: 0; }
  html, body { width: 1200px; height: 780px; overflow: hidden; }
  body {
    background: linear-gradient(135deg, var(--stage) 0%, var(--stage-dark) 100%);
    font-family: "Open Sans", Arial, sans-serif;
    position: relative;
  }
  .card {
    position: absolute;
    top: 240px;
    width: 520px;
    height: 300px;
    border-radius: 22px;
    background: var(--card);
    overflow: hidden;
    box-shadow: 0 18px 40px rgba(0,0,0,0.55);
  }
  .card--front { left: 60px; }
  .card--back { left: 620px; }
  .card__decor { position: absolute; inset: 0; width: 100%; height: 100%; }

  .brand {
    position: absolute;
    display: flex;
    align-items: center;
    gap: 10px;
    color: var(--white);
    font-weight: 800;
    text-transform: uppercase;
    letter-spacing: 1px;
    line-height: 1;
  }
  .brand__mark { background: var(--red); flex: none; }
  .brand__name { display: flex; flex-direction: column; gap: 4px; }
  .card--front .brand { left: 36px; top: 118px; font-size: 24px; }
  .card--front .brand__mark { width: 20px; height: 20px; }
  .card--back .brand { left: 50%; top: 50%; transform: translate(-50%, -50%); font-size: 34px; }
  .card--back .brand__mark { width: 28px; height: 28px; }
  .brand__suffix { font-size: 0.5em; letter-spacing: 4px; }

  .divider {
    position: absolute;
    left: 262px; top: 86px;
    width: 2px; height: 134px;
    background: var(--red);
  }
  .contact {
    position: absolute;
    left: 284px; top: 88px;
    color: var(--white);
  }
  .contact__name {
    color: var(--red);
    font-size: 22px;
    font-weight: 700;
    text-transform: uppercase;
    line-height: 1.1;
  }
  .contact__role { font-size: 13px; color: var(--muted); margin-bottom: 10px; }
  .contact__list { list-style: none; font-size: 13px; line-height: 1.55; }
  .contact__item { display: flex; align-items: center; gap: 7px; }
  .contact__icon { width: 12px; height: 12px; fill: var(--red); flex: none; }
  .contact__address { font-size: 13px; line-height: 1.45; margin-top: 4px; color: var(--muted); }
</style>
</head>
<body>

<section class="card card--front" aria-label="Business card front">
  <svg class="card__decor" viewBox="0 0 520 300" aria-hidden="true">
    <path d="M0 0 H150 Q70 18 0 62 Z" fill="var(--red)"/>
    <path d="M0 74 Q90 12 270 0" fill="none" stroke="var(--gold)" stroke-width="3"/>
    <path d="M520 300 H330 Q440 270 520 200 Z" fill="var(--red)"/>
    <path d="M250 300 Q420 262 520 182" fill="none" stroke="var(--gold)" stroke-width="3"/>
  </svg>

  <div class="brand">
    <span class="brand__mark"></span>
    <span class="brand__name"><span>Beacon</span><span>Guard</span><span class="brand__suffix">LLC</span></span>
  </div>

  <div class="divider"></div>

  <div class="contact">
    <p class="contact__name">Daniel Reyes</p>
    <p class="contact__role">Managing Director</p>
    <ul class="contact__list">
      <li class="contact__item">
        <svg class="contact__icon" viewBox="0 0 24 24"><path d="M6.6 10.8a15 15 0 0 0 6.6 6.6l2.2-2.2a1 1 0 0 1 1-.25 11.4 11.4 0 0 0 3.6.57 1 1 0 0 1 1 1V20a1 1 0 0 1-1 1A17 17 0 0 1 3 4a1 1 0 0 1 1-1h3.5a1 1 0 0 1 1 1c0 1.25.2 2.45.57 3.57a1 1 0 0 1-.25 1z"/></svg>
        123 456 789
      </li>
      <li class="contact__item">
        <svg class="contact__icon" viewBox="0 0 24 24"><path d="M2 5h20v14H2z M3.5 6.5 12 13l8.5-6.5" fill="var(--red)"/><path d="M3.5 6.5 12 13l8.5-6.5" fill="none" stroke="var(--card)" stroke-width="2"/></svg>
        info@beaconguard.com
      </li>
      <li class="contact__item">
        <svg class="contact__icon" viewBox="0 0 24 24"><circle cx="12" cy="12" r="10"/><path d="M2 12h20M12 2c3 3 3 17 0 20M12 2c-3 3-3 17 0 20" fill="none" stroke="var(--card)" stroke-width="1.6"/></svg>
        www.beaconguard.com
      </li>
    </ul>
    <p class="contact__address">Your address, City<br>State, Zip 1234</p>
  </div>
</section>

<section class="card card--back" aria-label="Business card back">
  <div class="brand">
    <span class="brand__mark"></span>
    <span class="brand__name"><span>Beacon</span><span>Guard</span><span class="brand__suffix">LLC</span></span>
  </div>
</section>

</body>
</html>
```